Website design for a high-end equestrian business

Design a website to replace current one. Clean, simple, elegant design. I run a business training show jumping riders and horses, as well as buying and selling high quality horses. I run my business from a beautiful yard in Co. Kildare, Ireland. Reference to Ireland and quality sport horses is important in the website.

Current website is www.orlathornbury.com. One page in particular that I need is a "Sport Horses" page as well as a "References" page. Layout for each to be similar to this one - https://www.brackenleaze.net/en/sporthorses

Another website I like the feel of is www.topcanterstable.com
Colour theme to be charcoal grey with elements of lighter grey and cream, as per logo. Charcoal grey to be somewhat transparent, otherwise it takes over too much. Cream colour is also to be subtle and not too beige.

Please note that Thornbury is one word.

Please note there are new photographs with which to work if desired.

Sick

Target Market(s)

Upmarket clients seeking high quality coaching services and high quality show jumping horses

Number of Pages Required

2 page

Font styles to use
Serif
Sans Serif

Colors

Designer to choose only greyscale colors for use in the design.

Requirements
Must have
• A clean, simple, elegant look to the final design. OVerall theme colours must be subtle and include charcoal grey, light grey and cream. A design that will work well for mobile also. Please include only photographs provided or on the old website.
Nice to have
• artistically integrated photographs. use of the logo.
Should not have
• Anything fussy.

```html
<!DOCTYPE html>
<html lang="en">
<head>
<meta charset="utf-8">
<title>Orla Thornbury – Current Horses</title>
<link href="https://fonts.googleapis.com/css2?family=Montserrat:wght@400;500;600;700;800&family=Cormorant+Garamond:wght@600&display=swap" rel="stylesheet">
<style>
:root{
  --charcoal:#454545;
  --charcoal-footer:#4f4f4f;
  --grey-text:#7d7d7d;
  --body-text:#6a6a6a;
  --cream:#d7cba0;
  --cream-light:#f3eedb;
  --white:#ffffff;
  --rule:#6a6a6a;
  --feed-blue:#2a8cf0;
}
*{box-sizing:border-box;margin:0;padding:0}
html,body{width:918px;height:1200px;overflow:hidden;background:var(--white)}
body{position:relative;font-family:"Montserrat",Arial,sans-serif;color:var(--body-text)}
.site-header{position:absolute;left:0;top:0;width:918px;height:93px;background:linear-gradient(#3c3c3c,#4a4a4a)}
.brand{position:absolute;left:126px;top:30px;font-family:"Cormorant Garamond",Georgia,serif;font-weight:600;font-size:26px;color:var(--cream);letter-spacing:.5px}
.social{position:absolute;display:flex;gap:9px}
.social span{display:block;border-radius:50%;background:var(--white)}
.header-social{left:697px;top:18px}
.header-social span{width:13px;height:13px}
.main-nav{position:absolute;left:313px;top:56px;display:flex;gap:20px;font-size:10px;font-weight:700;color:var(--white)}
.main-nav .active{color:var(--cream)}
.page-title{position:absolute;left:0;width:918px;top:166px;text-align:center;font-size:35px;font-weight:800;color:var(--grey-text);letter-spacing:-.5px}
.page-title em{font-style:normal;color:var(--cream)}
.intro{position:absolute;left:126px;top:244px;width:666px;font-size:9.6px;line-height:17.3px;text-align:justify;color:var(--body-text)}
.horse-grid{position:absolute;left:123px;top:396px;display:flex;gap:11px}
.horse-card{width:160px;text-align:center}
.horse-photo{height:154px;border-radius:4px;box-shadow:0 2px 5px rgba(0,0,0,.3)}
.p1{background:linear-gradient(160deg,#5b7aa8,#8c6a52 60%,#5a8a5a)}
.p2{background:linear-gradient(160deg,#6fa642,#8b5a33 55%,#4a7a30)}
.p3{background:linear-gradient(160deg,#e6e8ea,#7a4a2c 55%,#d8c048)}
.p4{background:linear-gradient(160deg,#9aa5ae,#6b4a30 50%,#2f4d8a)}
.horse-name{margin-top:28px;font-size:12px;font-weight:700;color:var(--grey-text);line-height:14.5px}
.footer-wave{position:absolute;left:0;top:650px;width:918px;height:550px}
.footer-brand{position:absolute;left:620px;top:810px;font-family:"Cormorant Garamond",Georgia,serif;font-weight:600;font-size:30px;color:var(--cream)}
.contact{position:absolute;left:120px;top:936px;font-size:9px;color:var(--white)}
.contact li{list-style:none;display:flex;gap:8px;align-items:flex-start;margin-bottom:17px;line-height:14.3px}
.contact svg{flex:none;margin-top:1px}
.footer-social{left:124px;top:1091px;gap:14px}
.footer-social span{width:17px;height:17px}
.quick-links{position:absolute;left:379px;top:934px;width:160px;text-align:center;font-size:9px;color:var(--white)}
.quick-links h3{font-size:9px;font-weight:700;text-decoration:underline;margin-bottom:16px}
.quick-links li{list-style:none;line-height:19.1px}
.feed{position:absolute;left:581px;top:940px;width:217px;height:162px;border-left:1px solid var(--rule);padding-left:14px;color:var(--white)}
.feed-scroll{position:absolute;right:0;top:0;width:2px;height:162px;background:#777}
.feed-scroll::before{content:"";position:absolute;left:0;top:0;width:2px;height:32px;background:var(--white)}
.post{position:relative;margin-top:9px;padding-right:12px}
.post + .post{margin-top:14px}
.post h4{font-size:8px;font-weight:700;color:var(--cream);display:flex;align-items:center;gap:10px}
.post h4 i{display:block;width:10px;height:10px;border-radius:50%;background:var(--feed-blue)}
.post p{margin-top:10px;font-size:6.8px;line-height:11.5px}
.post svg{position:absolute;right:12px;bottom:-6px}
.footer-bottom{position:absolute;left:0;top:1138px;width:918px;border-top:1px solid #666;padding-top:17px;text-align:center;font-size:8px;font-weight:500;color:var(--white)}
</style>
</head>
<body>
<header class="site-header">
  <div class="brand">Orla Thornbury</div>
  <div class="social header-social" aria-label="Social links"><span></span><span></span><span></span><span></span><span></span></div>
  <nav class="main-nav">
    <span class="active">HOME</span><span>ABOUT</span><span>HORSES</span><span>SPONSORS</span><span>FACILITIES &amp; SERVICES</span><span>GALLERY</span><span>CONTACT</span>
  </nav>
</header>

<h1 class="page-title">CURRENT <em>HORSES</em></h1>
<p class="intro">Orla has sourced, produced and sold many talented horses during her career. Back in her junior (U18) days, she produced the KWPN gelding Starlight as an unknown seven-year-old right up to CSI5* Grand Prix level, competing in Junior, Young Rider and Senior European Championships with him. Other mounts that she has produced include Maddox (1.60m), Caprice (1.60m), Celandine 4 (1.60m), Rumba des Prés (1.60m), Corvus van de Heide (1.60m), BTS Elwood (1.55m), Aster B (1.50m) Tango M'Alba (1.50m), BTS Kilbrack Kestrel (1.45m), Glenmore Tilly (1.45m), Copper Lane (1.40m) and Shanbally (1.40m), amongst many others. You'll find more information on current horses for sale and past references in the links below.</p>

<section class="horse-grid">
  <div class="horse-card"><div class="horse-photo p1" role="img" aria-label="Rider in navy jacket on a chestnut horse in the arena"></div><div class="horse-name">LOUGHMORE</div></div>
  <div class="horse-card"><div class="horse-photo p2" role="img" aria-label="Bay horse jumping a green hedge fence on grass"></div><div class="horse-name">BTS ELWOOD</div></div>
  <div class="horse-card"><div class="horse-photo p3" role="img" aria-label="Bay horse clearing a yellow and red show jump"></div><div class="horse-name">BTS KILBRACK<br>KESTREL</div></div>
  <div class="horse-card"><div class="horse-photo p4" role="img" aria-label="Bay horse jumping in front of a grandstand"></div><div class="horse-name">DKH SILVERBLUE</div></div>
</section>

<svg class="footer-wave" viewBox="0 0 918 550" aria-hidden="true">
  <defs>
    <linearGradient id="creamBand" x1="0" y1="0" x2="1" y2="0">
      <stop offset="0" stop-color="#ece4c6"/>
      <stop offset=".6" stop-color="#f7f3e4"/>
      <stop offset="1" stop-color="#ebe3c6"/>
    </linearGradient>
  </defs>
  <path d="M0 47 C180 150 480 140 700 45 C800 10 880 12 918 18 L918 550 L0 550 Z" fill="url(#creamBand)"/>
  <path d="M918 30 C800 22 700 75 560 145 C420 212 200 225 0 205 L0 550 L918 550 Z" fill="#4f4f4f"/>
  <path d="M180 172 C320 140 460 128 545 178 C450 152 320 158 180 172 Z" fill="#4f4f4f"/>
</svg>
<div class="footer-brand">Orla Thornbury</div>

<ul class="contact">
  <li><svg width="10" height="10" viewBox="0 0 10 10"><path d="M2 0 L4 2.5 L3 4 C4 6 5 7 6.5 7.5 L8 6.5 L10 8.5 L8.5 10 C4 9.5 .5 6 0 1.5 Z" fill="#fff"/></svg>+353 87 555 0142</li>
  <li><svg width="10" height="8" viewBox="0 0 10 8"><rect x=".5" y=".5" width="9" height="7" fill="none" stroke="#fff"/><path d="M.5 .5 L5 4.5 L9.5 .5" fill="none" stroke="#fff"/></svg>orla@orlathornbury.com</li>
  <li><svg width="9" height="11" viewBox="0 0 9 11"><path d="M4.5 0 C7 0 9 2 9 4.3 C9 7 4.5 11 4.5 11 C4.5 11 0 7 0 4.3 C0 2 2 0 4.5 0 Z" fill="#fff"/><circle cx="4.5" cy="4.3" r="1.6" fill="#4f4f4f"/></svg><span>Brackenhill Stables<br>Ballymore<br>Co. Kildare<br>Ireland<br>W91 Z4K2</span></li>
</ul>
<div class="social footer-social" aria-label="Social links"><span></span><span></span><span></span><span></span><span></span></div>

<nav class="quick-links">
  <h3>QUICK LINKS</h3>
  <ul><li>HOME</li><li>ABOUT</li><li>HORSES</li><li>GALLERY</li><li>CONTACT</li><li>SPONSORS</li><li>FACILITIES &amp; SERVICES</li></ul>
</nav>

<aside class="feed">
  <div class="feed-scroll"></div>
  <div class="post">
    <h4>ORLA THORNBURY <i></i></h4>
    <p>Still looking for another stable for Cavan if anyone has ended up with a spare last minute? Would need it from tomorrow evening!</p>
    <svg width="11" height="10" viewBox="0 0 11 10"><path d="M5.5 10 L1 5.5 C-1 3 1 0 3 0 C4.3 0 5 1 5.5 1.8 C6 1 6.7 0 8 0 C10 0 12 3 10 5.5 Z" fill="#fff"/></svg>
  </div>
  <div class="post">
    <h4>ORLA THORNBURY <i></i></h4>
    <p>Anyone looking to check the fit of their current saddle or purchase a new or good-as-new secondhand saddle, RK Equestrian/Corvane Sellier is your man! PM him for his next available dates in Ireland</p>
    <svg width="11" height="10" viewBox="0 0 11 10"><path d="M5.5 10 L1 5.5 C-1 3 1 0 3 0 C4.3 0 5 1 5.5 1.8 C6 1 6.7 0 8 0 C10 0 12 3 10 5.5 Z" fill="#fff"/></svg>
  </div>
</aside>

<footer class="footer-bottom">© 2020 Orla Thornbury. ALL RIGHTS RESERVED</footer>
</body>
</html>
```